Business Card Design Project

Business card based on attached logo

Todd Merrick
Todd@lorvantest.com
877-514-9073 ext. 318
Www.LorvanTest.com

Industry/Entity Type

Business

```html
<!DOCTYPE html>
<html lang="en">
<head>
<meta charset="utf-8">
<title>Lorvan Test – Business Cards</title>
<link href="https://fonts.googleapis.com/css2?family=Arimo:wght@400;700&display=swap" rel="stylesheet">
<style>
  :root {
    --brand-red: #ed1c24;
    --ink: #231f20;
    --paper: #ffffff;
    --mist: #e6e7e9;
    --backdrop: #9a5a2c;
  }
  * { margin: 0; padding: 0; box-sizing: border-box; }
  html, body { width: 1200px; height: 716px; overflow: hidden; }
  body {
    position: relative;
    background: var(--backdrop);
    font-family: "Arimo", Arial, sans-serif;
  }
  .card {
    position: absolute;
    width: 507px;
    height: 290px;
    overflow: hidden;
    box-shadow: 0 2px 6px rgba(0,0,0,.35);
  }
  .card--front { left: 51px; top: 37px; background: linear-gradient(#f4f4f5, var(--mist)); }
  .card--white { left: 623px; top: 37px; background: var(--paper); }
  .card--red   { left: 48px;  top: 379px; background: var(--brand-red); }
  .card--black { left: 629px; top: 381px; background: var(--ink); }

  .band {
    position: absolute; left: 0; right: 0; height: 33px;
    background: var(--brand-red); color: var(--paper);
    display: flex; align-items: center; justify-content: center;
  }
  .band--top { top: 0; font-weight: 700; font-size: 19px; letter-spacing: 2px; }
  .band--bottom { bottom: 0; font-size: 14px; letter-spacing: 2.5px; }
  .rule { position: absolute; left: 0; right: 0; height: 2px; background: var(--ink); }
  .rule--top { top: 36px; }
  .rule--bottom { bottom: 37px; }

  .wordmark {
    position: absolute; left: 0; right: 0;
    display: flex; align-items: center; justify-content: center; gap: 12px;
    font-weight: 700; line-height: 1;
  }
  .wordmark__square { width: 0.6em; height: 0.6em; flex: none; }
  .card--front .wordmark { top: 98px; font-size: 58px; color: var(--ink); }
  .card--front .wordmark__square { background: var(--brand-red); }
  .card--white .wordmark, .card--red .wordmark, .card--black .wordmark { top: 100px; font-size: 60px; }
  .card--white .wordmark { color: var(--brand-red); }
  .card--white .wordmark__square { background: var(--brand-red); }
  .card--red .wordmark, .card--black .wordmark { color: var(--paper); }
  .card--red .wordmark__square, .card--black .wordmark__square { background: var(--paper); }

  .contact {
    position: absolute; left: 0; right: 0; top: 225px;
    display: flex; justify-content: center; gap: 16px;
    font-size: 14px; color: var(--ink);
  }
  .contact__item { display: flex; align-items: center; gap: 5px; }
  .contact__icon { width: 11px; height: 11px; }

  .web {
    position: absolute; left: 0; right: 0; bottom: 20px;
    text-align: center; font-size: 15px; letter-spacing: 3px;
  }
  .card--white .web { color: var(--ink); }
  .card--red .web, .card--black .web { color: var(--paper); }
</style>
</head>
<body>
  <section class="card card--front">
    <div class="band band--top">Todd Merrick</div>
    <div class="rule rule--top"></div>
    <div class="wordmark"><span>LorvanTest</span><span class="wordmark__square"></span></div>
    <div class="contact">
      <span class="contact__item">
        <svg class="contact__icon" viewBox="0 0 12 12" aria-hidden="true"><path d="M2.5 1l2 2.5-1 1.2c.7 1.4 1.8 2.5 3 3.1l1.2-1 2.4 2-1.2 2C5 10.5 1.5 7 .8 2.3z" fill="#ed1c24"/></svg>
        877-514-9073 ext. 318
      </span>
      <span class="contact__item">
        <svg class="contact__icon" viewBox="0 0 12 12" aria-hidden="true"><rect x="0.5" y="2.5" width="11" height="7.5" fill="#ed1c24"/><path d="M0.5 2.5L6 7l5.5-4.5" stroke="#fff" stroke-width="1" fill="none"/></svg>
        Todd@lorvantest.com
      </span>
    </div>
    <div class="rule rule--bottom"></div>
    <div class="band band--bottom">www.LorvanTest.com</div>
  </section>

  <section class="card card--white">
    <div class="wordmark"><span>LorvanTest</span><span class="wordmark__square"></span></div>
    <p class="web">www.LorvanTest.com</p>
  </section>

  <section class="card card--red">
    <div class="wordmark"><span>LorvanTest</span><span class="wordmark__square"></span></div>
    <p class="web">www.LorvanTest.com</p>
  </section>

  <section class="card card--black">
    <div class="wordmark"><span>LorvanTest</span><span class="wordmark__square"></span></div>
    <p class="web">www.LorvanTest.com</p>
  </section>
</body>
</html>
```